Murder Mystery Buffet Dinner Fundraiser. An Evening of Murder, Mystery & Mayhem

Camp fundraiser needs a 7-element promotional package. The elements are 1) a save the date post card, 2) a two-sided invitation, 3) an invitation envelope, 4) a rsvp card, 5) a rsvp envelope, 6) the front page of a playbill size program book and 7) a 8.5" x 11" flyer. We hope to attract 125 donors to attend a fundraising murder mystery buffet dinner to support a 70 + year old residential summer camp. We would like the elements in the package to be consist with one another. The package should have a consistent theme. The theme should be mysterious, but playful and engaging.

Target Market(s)

middle class, 25 to 70 year olds

Other font styles liked:
• Broadway Playbill style

Colors

Designer to choose colors to be used in the design.

Requirements
Must have
• A mysterious, fun off Broadway feeling
Nice to have
• Perhaps a shadowy mysterious figure(s) or 5 playing cards, 10, jack, queen , king, ace, either individually or collectively, representing something sinister
Should not have
• Anything above a pg rating

```html
<!DOCTYPE html>
<html lang="en">
<head>
<meta charset="utf-8">
<title>Murder Mystery Dinner – Details</title>
<link href="https://fonts.googleapis.com/css2?family=Barlow:wght@500;600;700&display=swap" rel="stylesheet">
<style>
  :root {
    --ink: #020b12;
    --gold: #f7d416;
    --paper: #f2f2f2;
    --muted: #c9c9c9;
  }
  html, body { margin: 0; padding: 0; overflow: hidden; background: var(--ink); }
  .sheet {
    position: relative;
    width: 844px;
    height: 1200px;
    background: var(--ink);
    overflow: hidden;
    font-family: "Barlow", "Helvetica Neue", Arial, sans-serif;
    color: var(--paper);
    text-transform: uppercase;
  }
  .line {
    position: absolute;
    left: 0;
    width: 100%;
    text-align: center;
    transform: translateY(-50%);
    white-space: nowrap;
    line-height: 1;
  }
  .heading {
    color: var(--gold);
    font-weight: 600;
    font-size: 25px;
    letter-spacing: 6.5px;
  }
  .name { font-size: 16px; font-weight: 500; letter-spacing: 4.6px; }
  .committee .name { font-size: 17px; letter-spacing: 5.6px; }
  .detail { font-size: 16px; font-weight: 500; letter-spacing: 3.4px; }
  .detail strong { font-weight: 600; font-size: 18px; letter-spacing: 3.6px; }
  .detail .caterer { font-size: 23px; font-weight: 500; letter-spacing: 4px; }
  .or { color: var(--gold); font-size: 16px; font-weight: 600; letter-spacing: 3px; }
  .footer {
    font-size: 11px;
    font-weight: 700;
    letter-spacing: 3.6px;
    color: var(--muted);
  }
  .footer.link { color: var(--gold); }
</style>
</head>
<body>
<main class="sheet">
  <section class="board">
    <div class="line heading" style="top:84px">HVCC Board of Directors:</div>
    <div class="line name" style="top:126px">Mr. Daniel Whitford, Esq., President,</div>
    <div class="line name" style="top:157px">Rev. Samuel Ortega, Vice President,</div>
    <div class="line name" style="top:188px">Ms. Rachel Mendes,&nbsp; Ms Nora Kessler,</div>
    <div class="line name" style="top:219px">Rev. Thomas Ellery, Esq.,</div>
    <div class="line name" style="top:251px">Rev. Walter Brandt,&nbsp; Dr. Carla DeVane,</div>
    <div class="line name" style="top:282px">Ms.&nbsp; Irene Castillo-Ng,&nbsp; Mrs. Helen Porter,</div>
    <div class="line name" style="top:313px">Ms.&nbsp; Laura Bell Vantine,&nbsp; Mr. Peter Lund.</div>
  </section>

  <section class="event">
    <div class="line heading" style="top:397px">Event Details:</div>
    <div class="line detail" style="top:437px">Individual ticket are&nbsp; <strong>$225 per person,</strong></div>
    <div class="line detail" style="top:463px">RSVP by October 18, 2019.</div>
    <div class="line detail" style="top:494px">A delicious buffet dinner prepared by <span class="caterer">Lumen Catering.</span></div>
  </section>

  <section class="parking">
    <div class="line heading" style="top:566px">Parking:</div>
    <div class="line detail" style="top:599px">Valet Garage,</div>
    <div class="line detail" style="top:622px">41-43 W 48th St, NYC, NY 10036</div>
    <div class="line or" style="top:650px">Or</div>
    <div class="line detail" style="top:683px">Garage, 57 W 49th, NYC, NY 10036</div>
  </section>

  <section class="committee">
    <div class="line heading" style="top:767px">Murder Mystery Dinner Committee:</div>
    <div class="line name" style="top:809px">Rev. Vincent Morrow,</div>
    <div class="line name" style="top:838px">Rev. Thomas Ellery, Esq.,</div>
    <div class="line name" style="top:867px">Mr. Daniel Whitford, Esq.,</div>
    <div class="line name" style="top:895px">Dr. Carla DeVane,</div>
    <div class="line name" style="top:924px">Ms. Helen Porter,</div>
    <div class="line name" style="top:954px">Ms. Laura Vantine,</div>
    <div class="line name" style="top:983px">Ms. Julia Pascoe.</div>
  </section>

  <footer class="info">
    <div class="line footer" style="top:1056px">For more inforamation,</div>
    <div class="line footer" style="top:1073px">to purchase tickets , make a donation,</div>
    <div class="line footer" style="top:1091px">or become a sponsor, plase complete and return</div>
    <div class="line footer" style="top:1108px">the enclosed response card or visit</div>
    <div class="line footer link" style="top:1125px">www.hollowvalecamp.org/murdermysterydinner</div>
  </footer>
</main>
</body>
</html>
```